Brightfen Business Card Redesign & Logo Update

We need to update our business cards to something more modern and fresh. Brightfen can provide the current color schemes and old design examples, but welcome creativity in helping us with this redesign. PLEASE NOTE that we no longer utilize the "tree" and/or "leaf" imagery in our branding. If able would apprecaite an update on the quality of our "words only" logo in Ai. / PNG formats too.

Target Market(s)

Investors, landowners, corporate partners, contractors

Industry/Entity Type

Environmental Restoration & Conservation

Contact Information for Business Card

Logo, persons name, title, mailing address, phone and email, website url

Font styles to use
Other font styles liked:
• Merriweather

Requirements
Nice to have
• Logo, persons name, title, mailing address, phone and email, website url, but open to ideams
Should not have
• No all back backgrounds

```html
<!DOCTYPE html>
<html lang="en">
<head>
<meta charset="UTF-8">
<title>Brightfen Business Card</title>
<link rel="stylesheet" href="https://fonts.googleapis.com/css2?family=Oswald:wght@500;700&family=Roboto:wght@400;500&display=swap">
<style>
  :root {
    --stage: #262626;
    --orange: #ee7d00;
    --green: #147a35;
    --white: #ffffff;
    --ink: #1b1b1b;
  }
  * { box-sizing: border-box; margin: 0; padding: 0; }
  html, body { width: 1200px; height: 1015px; overflow: hidden; }
  body {
    background: var(--stage);
    position: relative;
    font-family: "Roboto", Arial, sans-serif;
  }
  .card {
    position: absolute;
    left: 220px;
    width: 760px;
    height: 434px;
    overflow: hidden;
    background: var(--orange);
  }
  .card--front { top: 50px; }
  .card--back { top: 531px; }

  .band {
    position: absolute;
    left: 0; right: 0;
    top: 300px;
    height: 46px;
    background: var(--green);
  }
  .band__url {
    position: absolute;
    top: 0;
    height: 46px;
    line-height: 46px;
    color: var(--white);
    font-size: 19px;
    letter-spacing: 2px;
  }
  .card--front .band__url { left: 0; right: 0; text-align: center; }
  .card--back .band__url { left: 330px; }

  .wordmark {
    position: absolute;
    font-family: "Oswald", "Arial Narrow", sans-serif;
    font-weight: 700;
    letter-spacing: 1px;
    line-height: 1;
  }
  .card--front .wordmark {
    left: 0; right: 0;
    top: 112px;
    text-align: center;
    font-size: 92px;
    color: var(--white);
  }

  .card--back .panel-white {
    position: absolute;
    left: 0; top: 0; bottom: 0;
    width: 400px;
    background: var(--white);
  }
  .card--back .band { z-index: 1; }
  .card--back .wordmark {
    left: 0;
    width: 400px;
    top: 118px;
    text-align: center;
    font-size: 72px;
    color: var(--green);
  }

  .contact {
    position: absolute;
    left: 436px;
    top: 62px;
    color: var(--white);
  }
  .contact__name {
    font-family: "Oswald", "Arial Narrow", sans-serif;
    font-weight: 700;
    font-size: 28px;
    line-height: 1.05;
    letter-spacing: 0.5px;
    text-transform: uppercase;
  }
  .contact__title { font-size: 17px; margin-bottom: 18px; }
  .contact__line {
    display: flex;
    align-items: center;
    gap: 8px;
    font-size: 17px;
    line-height: 1.45;
  }
  .contact__line svg { width: 16px; height: 16px; flex: none; }
  .contact__address { font-size: 17px; line-height: 1.35; margin-top: 14px; }
</style>
</head>
<body>
  <section class="card card--front" aria-label="Card front">
    <div class="wordmark">BRIGHTFEN</div>
    <div class="band"><span class="band__url">www.brightfen.com</span></div>
  </section>

  <section class="card card--back" aria-label="Card back">
    <div class="panel-white"></div>
    <div class="wordmark">BRIGHTFEN</div>
    <div class="contact">
      <p class="contact__name">Daniel Harlow</p>
      <p class="contact__title">Managing Director</p>
      <p class="contact__line">
        <svg viewBox="0 0 16 16" aria-hidden="true"><path fill="#147a35" d="M3.6 1.5l2.3 2.9-1.3 1.7c.9 2 2.5 3.6 4.5 4.6l1.7-1.3 2.9 2.3-1.4 2.3C7.2 13.6 2.4 8.8 1.3 2.9z"/></svg>
        044-987 650 312
      </p>
      <p class="contact__line">
        <svg viewBox="0 0 16 16" aria-hidden="true"><rect x="1" y="3" width="14" height="10" fill="#147a35"/><path d="M1 3l7 6 7-6" fill="none" stroke="#ee7d00" stroke-width="1.3"/></svg>
        hello@brightfen.com
      </p>
      <p class="contact__address">88, Marsh Row Lane<br>45917, Fenland Vale</p>
    </div>
    <div class="band"><span class="band__url">www.brightfen.com</span></div>
  </section>
</body>
</html>
```